Detail Shop Business card design

i need a business card design for my new detailing company called 'Brisk's Polish Works'. i want an all black and white design . simple, direct and to the point. i want the designer to choose a fitting font to match the logothe front should have logo, address, phone and email and the back side should have a slogan and text indicating that we offer services on anything including cars, trucks, motorcycles and RVs. slogan will read "we take pride in your ride"
maybe also very small on the back side the IG icon with Brisks_Polish_Works

phone 208.417.6352
address 3847 E Larkin Ave
Spokane WA 99214
email: BrisksPolish@mailvexo.com

Target Market(s)

all ages , auto enthusiasts

Industry/Entity Type

Automotive

Contact Information for Business Card

the front should have logo, address, phone and email and the back side should have a slogan and text indicating that we offer services on anything including cars, trucks, motorcycles and RVs. slogan will read "we take pride in your ride"

phone 208.417.6352
address 3847 E Larkin Ave
Spokane WA 99214

Colors
000000
ffffff

Requirements
Must have
• bold font and very simple design with good spacing
Nice to have
• anything creative from the designer indicating we service any types of vehicles
Should not have
• any colors ,

```html
<!DOCTYPE html>
<html lang="en">
<head>
<meta charset="utf-8">
<title>Brisk's Polish Works – Business Card</title>
<link href="https://fonts.googleapis.com/css2?family=Lato:ital,wght@0,400;0,700;0,900;1,700&display=swap" rel="stylesheet">
<style>
  :root {
    --ink: #000000;
    --paper: #ffffff;
    --backdrop: #e4e4e4;
    --card-w: 520px;
    --card-h: 297px;
  }
  * { box-sizing: border-box; margin: 0; padding: 0; }
  html, body { width: 1200px; height: 800px; overflow: hidden; }
  body {
    background: var(--backdrop);
    font-family: "Lato", Arial, sans-serif;
    color: var(--ink);
    display: flex;
    align-items: center;
    justify-content: center;
    gap: 40px;
  }
  .card {
    position: relative;
    width: var(--card-w);
    height: var(--card-h);
    background: var(--paper);
    overflow: hidden;
    box-shadow: 0 6px 18px rgba(0,0,0,0.12);
  }

  /* brand mark block: black band + name */
  .brand-band {
    position: absolute;
    top: 0;
    width: 74px;
    height: 112px;
    background: var(--ink);
  }
  .brand-name {
    position: absolute;
    width: 180px;
    text-align: center;
    font-weight: 900;
    font-size: 22px;
    line-height: 1.1;
    text-transform: uppercase;
    letter-spacing: 0.04em;
    color: var(--ink);
  }

  /* front */
  .card--front .corner-tab {
    position: absolute;
    left: 22px;
    top: 58px;
    width: 22px;
    height: 34px;
    background: var(--ink);
  }
  .card--front .contact {
    position: absolute;
    left: 58px;
    top: 56px;
    list-style: none;
    font-size: 12.5px;
    line-height: 1.45;
  }
  .contact li { display: flex; align-items: center; gap: 6px; }
  .contact svg { width: 11px; height: 11px; flex: none; }
  .card--front .brand-band { left: 372px; }
  .card--front .brand-name { left: 319px; top: 124px; }

  /* back */
  .card--back .brand-band { left: 223px; }
  .card--back .brand-name { left: 170px; top: 124px; }
  .card--back .slogan {
    position: absolute;
    left: 0;
    right: 0;
    top: 212px;
    text-align: center;
    font-style: italic;
    font-weight: 700;
    font-size: 13px;
    letter-spacing: 0.32em;
  }
</style>
</head>
<body>

  <section class="card card--front" aria-label="Card front">
    <div class="corner-tab"></div>
    <ul class="contact">
      <li>3847 E Larkin Ave</li>
      <li>Spokane WA 99214</li>
      <li>
        <svg viewBox="0 0 11 11" aria-hidden="true"><rect x="1" y="1" width="9" height="9" fill="none" stroke="#000" stroke-width="1"/></svg>
        208.417.6352
      </li>
      <li>
        <svg viewBox="0 0 11 11" aria-hidden="true"><rect x="0.5" y="2" width="10" height="7" fill="#000"/><path d="M0.5 2 L5.5 6 L10.5 2" fill="none" stroke="#fff" stroke-width="1"/></svg>
        BrisksPolish@mailvexo.com
      </li>
    </ul>
    <div class="brand-band"></div>
    <div class="brand-name">Brisk's<br>Polish Works</div>
  </section>

  <section class="card card--back" aria-label="Card back">
    <div class="brand-band"></div>
    <div class="brand-name">Brisk's<br>Polish Works</div>
    <p class="slogan">we take pride in your ride</p>
  </section>

</body>
</html>
```